Dew and Willow med spa needs an awesome eye catching billboard ad

We need a billboard ad design for a Med Spa with location sin Davenport and Windermere FL A medical spa where the beauty of nature meets the power of science to treat the whole person, mind, body and soul.

Marigold Radiance Med Spa is a medical spa where the beauty of nature meets the power of science to create gorgeous, youthful looking skin. Located in Davenport, Florida, but also serving Four Corners, Celebration, and Windermere, Florida, the talented professional team brings decades of experience in world-class skin care to provide holistic, science-backed aesthetic services and health coaching.

Industry/Entity Type

Spa

Colors
fbee3e
fece3e
eea4c8
e667a6
fbee3d

Requirements
Must have
• Locations in Lakeshore and Pine Hollow
Phone 407-555-0148
website www.dewandwillow-example.com

Boards for each:
Aesthetic Treatments
Cosmetic Injectables
Quoria facial
add color vs too many earthtones, to catch the eye perhaps using yellow, something that catches the eye and stands out from the normal everyday
Thank you!!!!
Nice to have
• Boards for each:
Aesthetic Treatments
Cosmetic Injectables
Quoria facial
add color vs too many earthtones, to catch the eye
photos that match services,
Thank you!!!!

```html
<!DOCTYPE html>
<html lang="en">
<head>
<meta charset="UTF-8">
<title>Quoria Facial Billboard – Marigold Radiance Med Spa</title>
<link href="https://fonts.googleapis.com/css2?family=PT+Sans:wght@400;700&display=swap" rel="stylesheet">
<style>
  :root {
    --page-bg: #ece8e2;
    --board-dark: #2f2e31;
    --board-dark-edge: #3a393c;
    --sun-yellow: #fbee3e;
    --marigold: #fece3e;
    --blush: #eea4c8;
    --orchid: #e667a6;
    --white: #ffffff;
    --brand-gold: #c7a86b;
    --pill-text: #2b2a2c;
  }
  * { margin: 0; padding: 0; box-sizing: border-box; }
  html, body {
    width: 1000px;
    height: 1200px;
    overflow: hidden;
    background: var(--page-bg);
  }
  .canvas {
    position: relative;
    width: 1000px;
    height: 1200px;
    display: flex;
    align-items: center;
    justify-content: center;
  }
  .billboard {
    width: 960px;
    height: 480px;
    display: block;
    font-family: "PT Sans", sans-serif;
  }
  .brand-name {
    fill: var(--brand-gold);
    font-weight: 400;
  }
  .brand-name--main { font-size: 34px; letter-spacing: 4px; }
  .brand-name--sub { font-size: 22px; letter-spacing: 7px; }
  .brand-mark { fill: var(--brand-gold); }
  .service-title {
    fill: var(--white);
    font-weight: 400;
    font-size: 76px;
  }
  .location-text {
    fill: var(--pill-text);
    font-size: 31px;
  }
  .phone-text {
    fill: var(--white);
    font-size: 68px;
    letter-spacing: 1px;
  }
  .web-text {
    fill: var(--white);
    font-size: 29px;
  }
  .icon-line {
    fill: none;
    stroke: var(--white);
    stroke-width: 3;
    stroke-linecap: round;
    stroke-linejoin: round;
  }
</style>
</head>
<body>
<main class="canvas">
  <svg class="billboard" viewBox="0 0 1310 655" xmlns="http://www.w3.org/2000/svg" aria-label="Quoria Facial billboard for Marigold Radiance Med Spa">
    <defs>
      <linearGradient id="darkPanel" x1="0" y1="0" x2="1" y2="1">
        <stop offset="0" stop-color="var(--board-dark-edge)"/>
        <stop offset="1" stop-color="var(--board-dark)"/>
      </linearGradient>
      <linearGradient id="yellowSweep" x1="0" y1="0" x2="0" y2="1">
        <stop offset="0" stop-color="var(--marigold)"/>
        <stop offset="0.5" stop-color="var(--sun-yellow)"/>
        <stop offset="1" stop-color="var(--marigold)"/>
      </linearGradient>
      <linearGradient id="yellowBand" x1="0" y1="0" x2="1" y2="0">
        <stop offset="0" stop-color="var(--marigold)"/>
        <stop offset="1" stop-color="var(--sun-yellow)"/>
      </linearGradient>
      <linearGradient id="pillFill" x1="0" y1="0" x2="0" y2="1">
        <stop offset="0" stop-color="var(--sun-yellow)"/>
        <stop offset="1" stop-color="var(--marigold)"/>
      </linearGradient>
      <linearGradient id="photoTone" x1="0" y1="0" x2="1" y2="1">
        <stop offset="0" stop-color="#d9d9db"/>
        <stop offset="0.35" stop-color="#e8c1a8"/>
        <stop offset="0.7" stop-color="#f0d2bf"/>
        <stop offset="1" stop-color="#e4e4e6"/>
      </linearGradient>
    </defs>

    <rect class="board-base" width="1310" height="655" fill="url(#darkPanel)"/>

    <path class="contact-band" d="M620,452 C880,500 1130,450 1310,388 L1310,655 L560,655 Z" fill="var(--orchid)"/>
    <path class="contact-band-edge" d="M620,448 C880,496 1130,446 1310,384" fill="none" stroke="var(--white)" stroke-width="10"/>
    <path class="contact-band-accent" d="M620,436 C880,484 1130,432 1310,366 L1310,382 C1130,444 880,494 620,446 Z" fill="url(#yellowBand)"/>

    <g class="photo-edge-stripes" fill="none">
      <path d="M560,0 C520,120 700,300 660,440 C630,560 585,620 560,655" stroke="var(--white)" stroke-width="108"/>
      <path d="M560,0 C520,120 700,300 660,440 C630,560 585,620 560,655" stroke="url(#yellowSweep)" stroke-width="88"/>
      <path d="M560,0 C520,120 700,300 660,440 C630,560 585,620 560,655" stroke="var(--blush)" stroke-width="34"/>
      <path d="M560,0 C520,120 700,300 660,440 C630,560 585,620 560,655" stroke="var(--white)" stroke-width="14"/>
    </g>

    <path class="service-photo" role="img" aria-label="Photo of a client receiving a facial treatment with a handheld device"
          d="M0,0 L560,0 C520,120 700,300 660,440 C630,560 585,620 560,655 L0,655 Z" fill="url(#photoTone)"/>

    <g class="brand">
      <circle class="brand-mark" cx="818" cy="112" r="14"/>
      <text class="brand-name brand-name--main" x="846" y="114">MARIGOLD RADIANCE</text>
      <text class="brand-name brand-name--sub" x="870" y="148">MED SPA</text>
    </g>

    <text class="service-title" x="980" y="290" text-anchor="middle">QUORIA FACIAL</text>

    <g class="location-pill">
      <rect x="760" y="349" width="440" height="60" rx="30" fill="url(#pillFill)"/>
      <g class="pin-icon" fill="none" stroke="var(--pill-text)" stroke-width="2.5">
        <path d="M805,392 C796,382 792,376 792,370 A9,9 0 0 1 810,370 C810,376 806,382 805,392 Z" fill="var(--pill-text)" stroke="none"/>
        <circle cx="801" cy="370" r="3.5" fill="var(--marigold)" stroke="none"/>
        <ellipse cx="801" cy="393" rx="9" ry="3"/>
      </g>
      <text class="location-text" x="820" y="390">Lakeshore and Pine Hollow</text>
    </g>

    <g class="contact">
      <g class="phone-icon">
        <path class="icon-line" d="M756,530 C752,540 762,560 780,570 C788,574 794,572 796,566 L790,558 L782,562 C774,558 768,550 766,542 L772,536 L766,526 C762,524 758,526 756,530 Z"/>
        <path class="icon-line" d="M782,536 A10,10 0 0 1 790,546"/>
        <path class="icon-line" d="M784,526 A20,20 0 0 1 800,542"/>
      </g>
      <text class="phone-text" x="815" y="574">407-555-0148</text>

      <g class="globe-icon">
        <circle class="icon-line" cx="766" cy="614" r="17"/>
        <circle class="icon-line" cx="766" cy="614" r="10"/>
        <ellipse class="icon-line" cx="766" cy="614" rx="4.5" ry="10"/>
        <line class="icon-line" x1="756" y1="614" x2="776" y2="614"/>
      </g>
      <text class="web-text" x="815" y="624">www.dewandwillow-example.com</text>
    </g>
  </svg>
</main>
</body>
</html>
```